Executive Business Card for Healthcare Company [Need Today]

I need a business card design for a healthcare company. The only branding the company has thus far is a logo. The cards will be utilized by company executives. The design I envision will be vibrant and appealing but with a corporate feel. They shouldn't be too casual or playful. I would like to complete this project TODAY if possible.

Target Market(s)

Healthcare vendors, other executives in healthcare and pharmaceuticals

Industry/Entity Type

Pharmaceutical

Contact Information for Business Card

See attachment

Font styles to use
Serif
Sans Serif

Colors

Designer to choose colors to be used in the design.

```html
<!DOCTYPE html>
<html lang="en">
<head>
<meta charset="utf-8">
<title>Corvane Therapeutics – Business Card</title>
<link href="https://fonts.googleapis.com/css2?family=Questrial&display=swap" rel="stylesheet">
<style>
  :root {
    --page-bg: #e9ecee;
    --teal: #36bfc6;
    --teal-deep: #1fb3bd;
    --ink: #2a2a2a;
    --grey: #6b6b6b;
    --card-white: #ffffff;
  }
  * { box-sizing: border-box; margin: 0; padding: 0; }
  html, body { width: 1200px; height: 880px; overflow: hidden; }
  body {
    background: var(--page-bg);
    font-family: "Questrial", "Century Gothic", sans-serif;
    display: flex;
    flex-direction: column;
    align-items: center;
    justify-content: center;
    gap: 44px;
  }
  .card {
    position: relative;
    width: 640px;
    height: 366px;
    border-radius: 22px;
    overflow: hidden;
    box-shadow: 0 6px 18px rgba(0,0,0,0.18);
  }
  .card--front { background: var(--teal); display: flex; align-items: center; justify-content: center; }
  .card--back { background: var(--card-white); }

  .brand__name { font-size: 36px; color: var(--ink); line-height: 1; white-space: nowrap; }
  .card--back .brand { position: absolute; left: 36px; top: 68px; }
  .card--back .brand__name { color: var(--teal-deep); font-size: 34px; }

  .divider {
    position: absolute; left: 36px; right: 36px; top: 212px;
    height: 1px; background: var(--teal);
  }
  .person { position: absolute; left: 36px; top: 162px; }
  .person__name { color: var(--teal-deep); font-size: 24px; line-height: 1.1; }
  .person__title { color: var(--grey); font-size: 17px; margin-top: 2px; line-height: 1.1; }
  .contacts { position: absolute; left: 36px; top: 236px; list-style: none; }
  .contacts li { display: flex; align-items: center; gap: 10px; color: var(--grey); font-size: 17px; margin-bottom: 9px; }
  .contacts svg { width: 20px; height: 20px; flex: none; }
  .office { position: absolute; right: 36px; top: 136px; text-align: right; }
  .office__company { color: var(--teal-deep); font-size: 17px; line-height: 1.2; }
  .office__line { color: var(--grey); font-size: 16px; margin-top: 2px; line-height: 1.2; }
</style>
</head>
<body>
  <section class="card card--front" aria-label="Card front">
    <div class="brand">
      <span class="brand__name">Corvane therapeutics</span>
    </div>
  </section>

  <section class="card card--back" aria-label="Card back">
    <div class="brand">
      <span class="brand__name">Corvane therapeutics</span>
    </div>

    <div class="office">
      <p class="office__company">Corvane Therapeutics, LLC</p>
      <p class="office__line">118 W Harmon Avenue</p>
      <p class="office__line">Fairview, GA 30512</p>
    </div>

    <div class="person">
      <p class="person__name">Daniel Marsh</p>
      <p class="person__title">Senior Director of Marketing</p>
    </div>
    <span class="divider"></span>

    <ul class="contacts">
      <li>
        <svg viewBox="0 0 20 20"><circle cx="10" cy="10" r="9" fill="none" stroke="#36bfc6" stroke-width="1.5"/><rect x="7" y="5" width="6" height="10" rx="1" fill="none" stroke="#36bfc6" stroke-width="1.3"/></svg>
        555-302-4418
      </li>
      <li>
        <svg viewBox="0 0 20 20"><circle cx="10" cy="10" r="9" fill="#36bfc6"/><path d="M6.5 6.5c0 4 3 7 7 7l1-1.6-2-1-1 1c-1.3-.6-2.3-1.6-2.9-2.9l1-1-1-2z" fill="#fff"/></svg>
        555-716-2054
      </li>
      <li>
        <svg viewBox="0 0 20 20"><circle cx="10" cy="10" r="9" fill="#36bfc6"/><rect x="5.5" y="7" width="9" height="6.5" fill="#fff"/><path d="M5.5 7l4.5 3.5L14.5 7" fill="none" stroke="#36bfc6" stroke-width="1"/></svg>
        dmarsh@corvanerx.com
      </li>
    </ul>
  </section>
</body>
</html>
```